Business Card Design Project

This is the first time we use our new logo. We need a business card that we can use both on our institutional corporate relationships and also that works for our staff that deals with consumers directly.

VELUNDA is a new company dedicated to empower consumers and to provide them with the best choices for specialized health care using the latest telemedicine technology (medicine at a distance via videoconference).

We want to print this cards in high quality materials and process. We will like designs that allow us to use UV spot varnish and other techniques that will differentiate us.

We are including Two different versions of Color logos. In addition we are including white over black background logos. Those can be used replacing the black for a color.

Please note this is the first time we will be creating any corporate materials with our new logo and colors.

Target Market(s)

34+ consumers of medium high and high socioeconomic levels.

Industry/Entity Type

Health

Requirements
Must have
• Our logo on its original colors
Should not have
• Any other graphical element or design that is not our logo

```html
<!DOCTYPE html>
<html lang="en">
<head>
<meta charset="utf-8">
<title>VELUNDA Business Cards</title>
<link rel="stylesheet" href="https://fonts.googleapis.com/css2?family=Jost:ital,wght@0,400;0,500;0,600;1,600&display=swap">
<style>
  :root {
    --page: #ecebe8;
    --navy: #1f5a85;
    --sky: #57b6e2;
    --teal: #1aa89a;
    --white: #ffffff;
    --ink: #2b2b2b;
    --silver-light: #e4e4e4;
    --silver-mid: #c9c9c9;
    --steel-dark: #2a2a2a;
  }
  * { box-sizing: border-box; margin: 0; padding: 0; }
  html, body { width: 788px; height: 1200px; overflow: hidden; }
  body { background: var(--page); font-family: "Jost", "Futura", sans-serif; position: relative; }

  .card {
    position: absolute; width: 300px; height: 525px; border-radius: 18px; overflow: hidden;
  }
  .card--front { left: 69px; top: 45px; }
  .card--white { left: 432px; top: 45px; background: var(--white); }
  .card--steel { left: 69px; top: 628px;
    background: linear-gradient(100deg, var(--steel-dark) 0%, #7a7a7a 35%, var(--silver-mid) 65%, var(--silver-light) 100%); }
  .card--navy { left: 430px; top: 632px; background: var(--navy); }

  .brand { position: absolute; left: 0; width: 100%; display: flex; flex-direction: column; align-items: center; }
  .brand__dot { border-radius: 50%; background: var(--teal); }
  .brand__name { font-weight: 600; letter-spacing: 2px; line-height: 1; }

  .card--front .brushed {
    position: absolute; left: 0; top: 0; width: 100%; height: 285px;
    background: linear-gradient(180deg, #d6d6d6 0%, var(--silver-light) 50%, #d9d9d9 100%);
  }
  .card--front .brand { top: 95px; gap: 46px; }
  .card--front .brand__dot { width: 70px; height: 70px; }
  .card--front .brand__name { font-size: 43px; color: var(--navy); }

  .name-band { position: absolute; left: 0; top: 285px; width: 300px; height: 52px; }
  .holder { position: absolute; left: 28px; top: 293px; color: #111; }
  .holder__name { font-size: 17px; font-weight: 600; }
  .holder__role { font-size: 13px; margin-top: 1px; }

  .details {
    position: absolute; left: 0; top: 337px; width: 100%; height: 188px; background: var(--navy);
    color: var(--white); padding: 26px 0 0 28px; font-size: 13.5px;
  }
  .details__row { display: flex; height: 26px; align-items: center; }
  .details__label { width: 52px; font-weight: 600; font-style: italic; }
  .details__value::before { content: ":"; margin-right: 8px; }
  .details__address { margin-top: 4px; line-height: 18px; font-size: 13px; }

  .card--white .brand { top: 120px; gap: 28px; }
  .card--white .brand__dot { width: 90px; height: 90px; }
  .card--white .brand__name { font-size: 48px; color: var(--navy); }

  .card--steel .brand { top: 130px; gap: 30px; }
  .card--steel .brand__dot { width: 170px; height: 170px; background: var(--white); }
  .card--steel .brand__name { font-size: 40px; color: var(--white); }

  .card--navy .brand { top: 155px; gap: 32px; }
  .card--navy .brand__dot { width: 100px; height: 100px; }
  .card--navy .brand__name { font-size: 44px; color: var(--white); }

  .web { position: absolute; left: 0; bottom: 28px; width: 100%; text-align: center; font-size: 17px; letter-spacing: 0.3px; }
  .card--white .web, .card--steel .web { color: var(--ink); }
  .card--navy .web { color: var(--white); }
</style>
</head>
<body>
  <section class="card card--front">
    <div class="brushed"></div>
    <div class="brand">
      <span class="brand__dot"></span>
      <span class="brand__name">VELUNDA</span>
    </div>
    <svg class="name-band" viewBox="0 0 300 52" aria-hidden="true">
      <polygon points="0,0 213,0 243,52 0,52" fill="var(--sky)"/>
      <polygon points="213,0 223,0 253,52 243,52" fill="#e8e8e8"/>
      <polygon points="223,0 300,0 300,52 253,52" fill="var(--teal)"/>
    </svg>
    <div class="holder">
      <p class="holder__name">Your Name</p>
      <p class="holder__role">Designation</p>
    </div>
    <div class="details">
      <p class="details__row"><span class="details__label">phone</span><span class="details__value">+12 345 67890</span></p>
      <p class="details__row"><span class="details__label">fax</span><span class="details__value">+12 345 67890</span></p>
      <p class="details__row"><span class="details__label">email</span><span class="details__value">info@website.com</span></p>
      <p class="details__row"><span class="details__label">web</span><span class="details__value">www.website.com</span></p>
      <p class="details__address">#0000, Street Name<br>Area Name, Country Code</p>
    </div>
  </section>

  <section class="card card--white">
    <div class="brand">
      <span class="brand__dot"></span>
      <span class="brand__name">VELUNDA</span>
    </div>
    <p class="web">www.website.com</p>
  </section>

  <section class="card card--steel">
    <div class="brand">
      <span class="brand__dot"></span>
      <span class="brand__name">VELUNDA</span>
    </div>
    <p class="web">www.website.com</p>
  </section>

  <section class="card card--navy">
    <div class="brand">
      <span class="brand__dot"></span>
      <span class="brand__name">VELUNDA</span>
    </div>
    <p class="web">www.website.com</p>
  </section>
</body>
</html>
```